Harbourline Electrical Solutions

On one side. LOGO (underneath:) Commercial Industrial Residential

- NAME & CONTACT DETAILS

Marcus T. Hollings
Project Manager

(Cell icon) (441) 555-0187
(Email icon) hlelectricalsolutions@mailvento.com
(Facebook & Instagram icons )@hlelectricalsolutions

Other side: LOGO - underneath ELECTRICAL CONSTRUCTION & MAINTENANCE . LED LIGHTING & AUTOMATION . LIFE SAFETY SYSTEMS (FIRE ALARM / SECURITY) . DATA & COMMUNICATION

```html
<!DOCTYPE html>
<html lang="en">
<head>
<meta charset="utf-8">
<title>Harbourline Electrical Solutions – Business Card</title>
<link rel="stylesheet" href="https://fonts.googleapis.com/css2?family=Montserrat:wght@300;400;500;600;700&display=swap">
<style>
  :root {
    --backdrop: #232325;
    --teal: #10566b;
    --white: #ffffff;
    --ink: #333333;
    --grey: #4a4a4a;
  }
  * { margin: 0; padding: 0; box-sizing: border-box; }
  html, body { width: 1200px; height: 1200px; overflow: hidden; }
  body {
    background: var(--backdrop);
    font-family: "Montserrat", sans-serif;
    position: relative;
  }
  .card {
    position: absolute;
    left: 300px;
    width: 600px;
    height: 360px;
  }
  .card-front { top: 220px; background: var(--teal); color: var(--white); }
  .card-back { top: 630px; background: var(--white); }

  .front-brand {
    position: absolute;
    left: 0; right: 0; top: 140px;
    text-align: center;
    font-weight: 500;
    font-size: 22px;
    line-height: 27px;
    letter-spacing: 3px;
    text-transform: uppercase;
  }
  .services {
    position: absolute;
    left: 0; right: 0; top: 302px;
    text-align: center;
    font-weight: 300;
    font-size: 11px;
    line-height: 16px;
    text-transform: uppercase;
  }

  .person { position: absolute; left: 41px; top: 240px; }
  .person-name {
    font-weight: 700;
    font-size: 18px;
    color: var(--teal);
    text-transform: uppercase;
    letter-spacing: 0.2px;
  }
  .person-role { font-size: 12.5px; color: var(--ink); margin-top: 1px; }
  .contact-list {
    list-style: none;
    margin-top: 14px;
    border-left: 1px solid var(--teal);
    padding-left: 6px;
  }
  .contact-item {
    display: flex;
    align-items: center;
    gap: 5px;
    font-weight: 600;
    font-size: 12.5px;
    color: var(--ink);
    height: 19.5px;
  }
  .contact-icon { width: 13px; height: 13px; flex: none; }

  .back-brand {
    position: absolute;
    left: 488px; top: 315px;
    transform-origin: 0 0;
    transform: rotate(-90deg);
    font-weight: 500;
    font-size: 16px;
    line-height: 18.5px;
    letter-spacing: 2.5px;
    color: var(--teal);
    text-transform: uppercase;
    white-space: nowrap;
  }
</style>
</head>
<body>
  <section class="card card-front">
    <div class="front-brand">Harbourline<br>Electrical<br>Solutions</div>
    <p class="services">
      Electrical Construction &amp; Maintenance • LED Lighting &amp; Automation<br>
      • Life Safety Systems (Fire Alarm / Security) • Data &amp; Communication
    </p>
  </section>

  <section class="card card-back">
    <div class="person">
      <h1 class="person-name">Marcus T. Hollings</h1>
      <p class="person-role">Project Manager</p>
      <ul class="contact-list">
        <li class="contact-item">
          <svg class="contact-icon" viewBox="0 0 16 16" aria-hidden="true">
            <circle cx="8" cy="8" r="7" fill="none" stroke="#10566b" stroke-width="1"/>
            <path d="M5.2 4.5l1.3-.3.8 1.8-.9.7c.4.9 1 1.5 1.9 1.9l.7-.9 1.8.8-.3 1.3c-3 .2-5.5-2.3-5.3-5.3z" fill="#10566b"/>
          </svg>
          (441) 555-0187
        </li>
        <li class="contact-item">
          <svg class="contact-icon" viewBox="0 0 16 16" aria-hidden="true">
            <circle cx="8" cy="8" r="7" fill="none" stroke="#10566b" stroke-width="1"/>
            <rect x="4.3" y="5.3" width="7.4" height="5.4" fill="none" stroke="#10566b" stroke-width="1"/>
            <path d="M4.3 5.3L8 8.3l3.7-3" fill="none" stroke="#10566b" stroke-width="1"/>
          </svg>
          hlelectricalsolutions@mailvento.com
        </li>
        <li class="contact-item">
          <svg class="contact-icon" viewBox="0 0 16 16" aria-hidden="true">
            <circle cx="8" cy="8" r="7" fill="none" stroke="#10566b" stroke-width="1"/>
          </svg>
          <svg class="contact-icon" viewBox="0 0 16 16" aria-hidden="true">
            <circle cx="8" cy="8" r="7" fill="none" stroke="#10566b" stroke-width="1"/>
          </svg>
          @hlelectricalsolutions
        </li>
      </ul>
    </div>
    <div class="back-brand">Harbourline<br>Electrical<br>Solutions</div>
  </section>
</body>
</html>
```